Business Card Design

I already have a company logo for my company. I have a logo for the manufacturer we represent. I want a professional business card design.

```html
<!DOCTYPE html>
<html lang="en">
<head>
<meta charset="utf-8">
<title>Beacon Alert Group – Business Card</title>
<link rel="stylesheet" href="https://fonts.googleapis.com/css2?family=Montserrat:wght@500;700;800&family=Open+Sans:wght@400;600&display=swap">
<style>
  :root {
    --bg: #2a2a2d;
    --card: #1d1c20;
    --card-pattern: #242327;
    --red: #e3202a;
    --gold: #c9a227;
    --white: #ffffff;
    --muted: #e9e9ec;
  }
  * { box-sizing: border-box; margin: 0; padding: 0; }
  html, body {
    width: 1200px; height: 780px; overflow: hidden;
    background: var(--bg);
  }
  .canvas {
    position: relative; width: 1200px; height: 780px;
    display: flex; align-items: center; justify-content: center; gap: 48px;
  }
  .card {
    position: relative;
    width: 532px; height: 310px;
    border-radius: 26px;
    background: var(--card);
    border: 3px solid var(--red);
    overflow: hidden;
  }
  /* Front */
  .card-front .pattern {
    position: absolute; inset: 0;
    background: linear-gradient(135deg, var(--card-pattern), var(--card) 70%);
  }
  .brand {
    position: absolute; left: 0; right: 0; top: 50%;
    transform: translateY(-50%);
    display: flex; flex-direction: column; align-items: center; gap: 14px;
  }
  .brand-row { display: flex; align-items: center; gap: 14px; }
  .brand-dot {
    width: 26px; height: 26px; border-radius: 50%;
    background: var(--red);
  }
  .brand-name {
    font-family: "Montserrat", sans-serif;
    font-weight: 800; font-size: 34px; letter-spacing: 1px;
    text-transform: uppercase; color: var(--white);
  }
  .brand-rule { width: 330px; height: 3px; background: var(--gold); }

  /* Back */
  .person {
    position: absolute; left: 44px; top: 104px;
    font-family: "Montserrat", sans-serif;
  }
  .person-name { font-size: 33px; font-weight: 700; color: var(--white); line-height: 1.1; }
  .person-name .first { color: var(--red); }
  .person-title { font-size: 16px; font-weight: 500; color: var(--white); margin-top: 4px; letter-spacing: .3px; }
  .divider {
    position: absolute; left: 300px; top: 70px;
    width: 1px; height: 104px;
    background: linear-gradient(var(--card), var(--gold), var(--card));
  }
  .contacts {
    position: absolute; left: 322px; top: 84px;
    list-style: none;
    font-family: "Open Sans", sans-serif; font-size: 14px; color: var(--muted);
    display: flex; flex-direction: column; gap: 9px;
  }
  .contact { display: flex; align-items: center; gap: 8px; }
  .contact svg { width: 14px; height: 14px; flex: none; }
  .address {
    position: absolute; left: 44px; right: 30px; bottom: 44px;
    font-family: "Open Sans", sans-serif; font-size: 15px; color: var(--white);
    letter-spacing: .2px;
  }
</style>
</head>
<body>
<main class="canvas">
  <section class="card card-front" aria-label="Business card front">
    <div class="pattern" role="img" aria-label="Faint repeating brand pattern over dark background"></div>
    <div class="brand">
      <div class="brand-row">
        <span class="brand-dot"></span>
        <span class="brand-name">Beacon Alert Group</span>
      </div>
      <div class="brand-rule"></div>
    </div>
  </section>

  <section class="card card-back" aria-label="Business card back">
    <div class="person">
      <p class="person-name"><span class="first">Lena</span> Marsh</p>
      <p class="person-title">Managing Director</p>
    </div>
    <div class="divider"></div>
    <ul class="contacts">
      <li class="contact">
        <svg viewBox="0 0 24 24" aria-hidden="true"><path fill="#e3202a" d="M6.6 10.8a15.1 15.1 0 0 0 6.6 6.6l2.2-2.2a1 1 0 0 1 1-.25 11.4 11.4 0 0 0 3.6.57 1 1 0 0 1 1 1V20a1 1 0 0 1-1 1A17 17 0 0 1 3 4a1 1 0 0 1 1-1h3.5a1 1 0 0 1 1 1c0 1.25.2 2.45.57 3.57a1 1 0 0 1-.25 1z"/></svg>
        (555) 214-6083
      </li>
      <li class="contact">
        <svg viewBox="0 0 24 24" aria-hidden="true"><path fill="#e3202a" d="M3 5h18a1 1 0 0 1 1 1v12a1 1 0 0 1-1 1H3a1 1 0 0 1-1-1V6a1 1 0 0 1 1-1zm9 7.5L4 7.2V8l8 5.3L20 8v-.8z"/></svg>
        hello@beaconalert.com
      </li>
      <li class="contact">
        <svg viewBox="0 0 24 24" aria-hidden="true"><circle cx="12" cy="12" r="9.5" fill="none" stroke="#e3202a" stroke-width="2"/><path d="M2.5 12h19M12 2.5c3 3 3 16 0 19M12 2.5c-3 3-3 16 0 19" fill="none" stroke="#e3202a" stroke-width="1.6"/></svg>
        www.beaconalert.com
      </li>
    </ul>
    <p class="address">1840 Lakeside Ave. Suite 310 Riverton, TX 76540</p>
  </section>
</main>
</body>
</html>
```